Contest - label design for a health related product

Velmora is a brand for a set of 4 different colloids, namely colloidal silver, colloidal gold, colloidal zinc and colloidal copper. These colloids have a positive impact on peopleā€˜s health. Each colloid has different impacts on the health.

A colloid is a substance microscopically dispersed evenly throughout another substance. In our case the substance is water and a metal which has been broken down by an electrochemical process to the smallest possible particle size (also called nano-particles). Please google "colloidal silver".

Your job is to design a label (70 mm high x 132 mm wide) for each of the 4 types of colloids. The label will be printed as a sticker which then in return will be placed on a bottle made out of brown glass (see attachment). The 4 labels should have the respective logo (see attachments) and colors that represent the respective type of colloid, i.e. for colloidal silver, there should be a silverish color used as a theme on the label and so on. You should first create one label for colloidal silver. If we like the design we will select you and then you can make the 3 remaining labels with the respective color and logo.

What information goes on the label:

On the left side there will be text and a graphic of a bar code:
Distribution through
ABC Company
Address
Postal Code City
Country

A graphic of a bar code

Made in Austria
Copyright by CDE company, registration no. 123456,

In the middle:
The logo (see attachment)
The product, i.e. "Kolloidales Silber" (it's in German)
The concentration in ppm, i.e. 25 ppm
The amount in ml, i.e. 500 ml

On the right side:
Store in a cold place and away from electrical fields, including the refrigerator and the micro wave. Do not immerse any metal objects into the colloid, such as a metal table spoon.

Ingredients: Aqua bidest. and nano particles of silver.

We have attached a label that we found on Artquill. We like the colors and the style.

We need the file in illustrator with editable fonts.

As soon as we have designs from 10 different designers, we will guarantee the project!
Updates

Dear All,

First of all, we would like to thank everyone who participated in this project. It was a very difficult decision as there were a lot of top designs. You guys are incredibly creative.

Thank you and all the best for 2013! Keep on the good jobs you guys are doing.

Target Market(s)

Health concious people between 25 and 70

Industry/Entity Type

Electrical

Requirements
Must have
• - the attached logos (1 for each type of colloid)
- clear
- vivid colors, matching the logo
- minimalistic
- abstract
Should not have
• - Heavy, dark colors
- Text that hints to health benefits (just use the text we have given you)

```html
<!DOCTYPE html>
<html lang="en">
<head>
<meta charset="utf-8">
<title>Velmora Kolloidales Silber – Label</title>
<link rel="stylesheet" href="https://fonts.googleapis.com/css2?family=Jost:wght@400;500;600;700&family=Oswald:wght@600;700&display=swap">
<style>
  :root {
    --yellow: #f7c514;
    --yellow-soft: #fde68a;
    --teal: #17a3b8;
    --teal-dark: #0f8ea3;
    --teal-light: #8fd6df;
    --blue: #2f6db5;
    --ink: #111111;
    --white: #ffffff;
    --page: #ffffff;
  }
  * { box-sizing: border-box; margin: 0; padding: 0; }
  html, body {
    width: 1200px; height: 927px; overflow: hidden;
    background: var(--page);
  }
  .canvas { position: relative; width: 1200px; height: 927px; }
  .label {
    position: absolute; left: 52px; top: 96px;
    width: 920px; height: 553px;
    background: var(--white);
    overflow: hidden;
    font-family: "Jost", sans-serif;
    color: var(--ink);
  }
  .label-art { position: absolute; inset: 0; width: 920px; height: 553px; }
  .brand-plate {
    position: absolute; left: 345px; top: -6px;
    width: 218px; height: 142px;
    background: var(--yellow-soft);
    border: 4px solid var(--yellow);
    border-radius: 0 0 14px 14px;
    display: flex; align-items: center; justify-content: center;
  }
  .brand-dot {
    width: 62px; height: 62px; border-radius: 50%;
    background: var(--blue);
  }
  .brand-name {
    position: absolute; left: 300px; width: 310px; top: 140px;
    text-align: center;
    font-weight: 600;
    font-size: 36px; color: var(--blue); letter-spacing: -0.5px;
  }
  .product-name {
    position: absolute; left: 280px; width: 350px; top: 190px;
    text-align: center;
    font-family: "Oswald", sans-serif; font-weight: 700;
    font-size: 64px; line-height: 68px; color: var(--ink);
  }
  .volume {
    position: absolute; left: 300px; width: 310px; top: 334px;
    text-align: center;
    font-family: "Oswald", sans-serif; font-weight: 600;
    font-size: 32px; line-height: 40px; color: var(--blue);
  }
  .distributor {
    position: absolute; left: 10px; width: 236px; top: 128px;
    text-align: center; font-size: 22px; line-height: 24px;
  }
  .distributor strong { font-weight: 700; }
  .code-box {
    position: absolute; left: 40px; top: 310px;
    width: 180px; height: 102px;
    background: var(--white); border: 1px solid #9aa4a8;
  }
  .origin {
    position: absolute; left: 20px; width: 230px; top: 440px;
    text-align: center; color: var(--white);
    font-size: 17px; line-height: 22px; font-weight: 500;
  }
  .storage {
    position: absolute; left: 668px; width: 232px; top: 22px;
    text-align: center; color: var(--white);
    font-size: 17px; line-height: 21px; font-weight: 600;
  }
  .ingredients {
    position: absolute; left: 688px; width: 240px; top: 300px;
    text-align: center; font-size: 21px; line-height: 23px;
  }
  .ingredients .heading { font-weight: 500; }
  .concentration {
    position: absolute; right: 54px; top: 470px;
    font-family: "Oswald", sans-serif; font-weight: 700;
    font-size: 30px; line-height: 38px; color: var(--white);
  }
</style>
</head>
<body>
<div class="canvas">
  <section class="label" aria-label="Kolloidales Silber bottle label">
    <svg class="label-art" viewBox="0 0 920 553" aria-hidden="true">
      <defs>
        <linearGradient id="topBand" x1="0" y1="0" x2="0" y2="1">
          <stop offset="0" stop-color="#f7c514"/>
          <stop offset="0.55" stop-color="#fbe38a"/>
          <stop offset="1" stop-color="#ffffff"/>
        </linearGradient>
        <linearGradient id="tealFill" x1="0" y1="0" x2="1" y2="1">
          <stop offset="0" stop-color="#0f8ea3"/>
          <stop offset="0.5" stop-color="#1aaabd"/>
          <stop offset="1" stop-color="#23b2c3"/>
        </linearGradient>
        <linearGradient id="sheen" x1="0" y1="0" x2="1" y2="0">
          <stop offset="0" stop-color="#ffffff" stop-opacity="0.1"/>
          <stop offset="0.5" stop-color="#ffffff" stop-opacity="0.7"/>
          <stop offset="1" stop-color="#ffffff" stop-opacity="0.1"/>
        </linearGradient>
      </defs>
      <rect class="top-band" x="0" y="0" width="920" height="70" fill="url(#topBand)"/>
      <path class="storage-panel" d="M618,0 H920 V250 C820,270 700,250 650,170 C625,120 618,60 618,0 Z" fill="#f7c514"/>
      <path class="wave-back" d="M0,248 C200,236 350,332 520,402 C680,462 830,440 920,426 L920,553 L0,553 Z" fill="#8fd6df"/>
      <path class="wave-main" d="M0,264 C200,254 340,352 500,422 C650,482 820,458 920,442 L920,553 L0,553 Z" fill="url(#tealFill)"/>
      <path class="wave-sheen" d="M150,292 C330,322 480,428 640,474 C760,506 860,492 920,480 L920,492 C860,504 760,520 630,486 C470,440 320,334 150,292 Z" fill="url(#sheen)"/>
    </svg>

    <div class="brand-plate"><span class="brand-dot"></span></div>
    <div class="brand-name">Velmora Gold</div>
    <h1 class="product-name">Kolloidales<br>Silber</h1>
    <div class="volume">500 ml</div>

    <div class="distributor">
      Distribution through<br>
      <strong>ABC Company</strong><br>
      Address<br>
      Postal Code City<br>
      Country
    </div>
    <div class="code-box"></div>
    <div class="origin">
      Made in Austria<br>
      Copyright by<br>
      CDE Company,<br>
      Registration No. 123456,
    </div>

    <p class="storage">
      Store in a cold place and away from electrical fields, including the refrigerator and the micro wave. Do not immerse any metal objects into the colloid, such as a metal table spoon.
    </p>
    <div class="ingredients">
      <span class="heading">Ingredients:</span><br>
      Aqua bidest and<br>
      nano particles of silver.
    </div>
    <div class="concentration">25 ppm</div>
  </section>
</div>
</body>
</html>
```